Maranoola Wines - web page for new Australian wine label

We need a landing page for our wine company. Maranoola is a family owned company, we grow the gapes, and make the wine in the Clare valley. Daniel Whitlock is the winemaker and is well known for his style, which is all about the fruit flavour rather than wood or age influences. Maranoola is Abriginal for 2 hills and a water source. We hand pick, hand plunge, foot crush resulting in elegant wine. Little to no additives, minimal filtering, single vineyard wines. Handcrafted with small releases of only the best fruit from carefully selected rows and bunches. The Clare valley is located two hours North of Adelaide, is known for cool climate and slow ripening, resulting in wines that have an elegant mouth feel, with bright colour and outstanding flavours. Our Brookmere vineyard has a Eastern aspect, gathering morning sun and escaping the hot afternoons, and in our opinion is on of the prettiest valleys in the world. Only 1000 cases per annum of the very best handpicked fruit, from the best rows. We hope you enjoy the Maranoola style, the reds are lighter in colour, fruit driven palate, more old world influence and the Riesling is on the dry side with fresh citrus. Minimal additives and filtering, our aim was to make wine with minimal influence from wine making. Handcrafted wines.

Target Market(s)

females 18 - 60 are the ones that buy 70 percent of wine, so whilst men are also a target, its the ladies we seek to appeal to.

Industry/Entity Type

It Company

Number of Pages Required

4 page

Font styles to use
Serif

Requirements
Must have
• Eye catching front page that makes me feel like i am ordering from quality company, that cares for what they do. Easy to use ordering, and delivery instructions.
• postage is $14.90 per case Australia wide.
• www.maranoolawines-example.com
Nice to have
• I want to see a fun and family oriented business that cares for the wine, we dont make a lot, its buckets and feet. But its wine made wanting to be the best in the world, we dont cut corners on quality. Handcrafted
Should not have
• dont really have any thoughts here, looking for all ideas

```html
<!DOCTYPE html>
<html lang="en">
<head>
<meta charset="utf-8">
<title>Maranoola Wines</title>
<link href="https://fonts.googleapis.com/css2?family=Bodoni+Moda:ital,wght@0,400;0,600;1,400&display=swap" rel="stylesheet">
<style>
  :root{
    --wine:#5c1732;
    --wine-dark:#4a1026;
    --rose:#d49ab9;
    --rose-line:#b47f9c;
    --ink:#4a1a2c;
    --white:#ffffff;
    --story-bg:#f4ece8;
  }
  *{box-sizing:border-box;margin:0;padding:0}
  html,body{width:1200px;height:3888px;overflow:hidden}
  body{position:relative;background:var(--white);font-family:"Bodoni Moda",serif;color:var(--ink)}
  .abs{position:absolute}

  /* header */
  .site-header{left:0;top:0;width:1200px;height:62px;background:var(--white)}
  .brand{left:60px;top:8px;display:flex;align-items:center;gap:10px;color:var(--rose);font-size:36px;line-height:46px}
  .brand-dot{width:10px;height:10px;border-radius:50%;background:var(--rose)}
  .nav a{position:absolute;top:14px;font-size:22px;color:var(--wine);text-decoration:none}
  .nav .active::before{content:"";position:absolute;left:-18px;right:-18px;top:-14px;height:8px;background:var(--wine)}

  /* hero */
  .hero{left:0;top:62px;width:1200px;height:568px;
    background:radial-gradient(ellipse at 70% 40%,#5a4a40 0%,#2e221e 45%,#1b1412 100%)}
  .hero-title{left:0;top:240px;width:1200px;text-align:center;color:var(--white);font-style:italic;font-size:46px;line-height:60px}
  .btn{display:flex;align-items:center;justify-content:center;background:var(--rose);color:var(--white);border-radius:8px}
  .hero-btn{left:456px;top:407px;width:290px;height:52px;font-size:20px;font-weight:600;letter-spacing:1px}

  /* section bands */
  .band{left:0;width:1200px;height:70px;background:var(--wine);color:var(--white);font-size:28px;
    display:flex;align-items:center;justify-content:center;box-shadow:0 6px 8px rgba(60,10,30,.35)}

  /* wine cards */
  .wine-card{height:245px;border:2px solid var(--rose-line);background:var(--white)}
  .wine-photo{left:0;top:0;width:231px;height:100%}
  .price-tag{left:-6px;top:16px;width:238px;height:36px;background:var(--wine);color:var(--white);
    font-size:18px;display:flex;align-items:center;justify-content:center}
  .wine-name{left:278px;top:10px;font-size:23px;color:var(--wine)}
  .wine-notes{left:278px;top:50px;width:260px;font-size:17px;line-height:24px;color:var(--wine)}
  .wine-pairing{left:278px;top:198px;font-size:17px;color:var(--wine)}
  .icon{width:24px;height:24px}
  .icon-flavor{left:250px;top:54px}
  .icon-pair{left:250px;top:198px}

  /* story */
  .story{left:0;top:1392px;width:1200px;height:430px;
    background:radial-gradient(ellipse at 50% 30%,#efe1dc 0%,var(--story-bg) 60%,#e9dcd7 100%)}
  .story-text{left:205px;top:56px;width:790px;text-align:center;font-size:12.5px;line-height:19px;color:var(--ink)}
  .story-text p{margin-bottom:12px}

  /* gallery */
  .gallery-item{width:350px;height:240px}
  .g-vines{background:linear-gradient(160deg,#5d7a2e,#3b3a1e 55%,#6b8f34)}
  .g-pour{background:radial-gradient(ellipse at 40% 55%,#8e1c2e,#3a1418 55%,#1c1210)}
  .g-bottles{background:linear-gradient(120deg,#b9473f,#2a1512 45%,#6a3a24 85%)}

  /* contact */
  .field{left:187px;width:811px;border:2px solid var(--rose-line);font-size:16px;color:var(--ink);padding:6px 30px}
  .send-btn{left:187px;top:3354px;width:811px;height:62px;font-size:26px;border-radius:10px}

  /* follow */
  .social{top:3678px;width:67px;height:66px;border-radius:14px;background:var(--wine)}
  .footer{left:0;top:3857px;width:1200px;height:31px;background:var(--wine)}
</style>
</head>
<body>

<header class="abs site-header">
  <div class="abs brand"><span class="brand-dot"></span>Maranoola</div>
  <nav class="nav">
    <a class="active" style="left:698px">Home</a>
    <a style="left:818px">Our Story</a>
    <a style="left:982px">Cart</a>
  </nav>
</header>

<section class="abs hero" role="img" aria-label="Wine bottles on a wooden table in a softly lit cellar">
</section>
<h1 class="abs hero-title" style="font-weight:400">Try Our Wonderful<br>Wine Selections</h1>
<a class="abs btn hero-btn">SHOP NOW</a>

<h2 class="abs band" style="top:632px;font-weight:400">Our Wines</h2>

<!-- wine card template repeated -->
<article class="abs wine-card" style="left:36px;top:770px;width:545px">
  <div class="abs wine-photo" role="img" aria-label="Rows of red wine glasses on a tasting table" style="background:linear-gradient(170deg,#d9d3d6,#8a5060 60%,#5a2030)"></div>
  <div class="abs price-tag">Price: $14.95</div>
  <h3 class="abs wine-name" style="font-weight:400">2016 Reserve Cabarnet</h3>
  <svg class="abs icon icon-flavor" viewBox="0 0 24 24" fill="none" stroke="#5c1732" stroke-width="1.5"><circle cx="12" cy="12" r="11"/><path d="M8 6h8c0 4-2 6-4 6s-4-2-4-6zM12 12v6M9 18h6"/></svg>
  <p class="abs wine-notes">Flavor profile: ectetur, adipisci velit, sed quia non numquam eius modi tempora incidunt ut labore et dolore magnam aliquam quaerat voluptatem.</p>
  <svg class="abs icon icon-pair" viewBox="0 0 24 24" fill="none" stroke="#5c1732" stroke-width="1.5"><circle cx="12" cy="12" r="11"/><path d="M6 16l12-6v6zM10 14.5v.5M14 13v.5"/></svg>
  <p class="abs wine-pairing" style="left:278px">Best Pairing: Cheese</p>
</article>

<article class="abs wine-card" style="left:607px;top:770px;width:554px">
  <div class="abs wine-photo" role="img" aria-label="Two glasses of sparkling wine in warm candlelight" style="background:radial-gradient(ellipse at 50% 60%,#f2b55a,#b0602a 55%,#5a2a18)"></div>
  <div class="abs price-tag">Price: $14.95</div>
  <h3 class="abs wine-name" style="font-weight:400">2016 Reserve Cabarnet</h3>
  <svg class="abs icon icon-flavor" viewBox="0 0 24 24" fill="none" stroke="#5c1732" stroke-width="1.5"><circle cx="12" cy="12" r="11"/><path d="M8 6h8c0 4-2 6-4 6s-4-2-4-6zM12 12v6M9 18h6"/></svg>
  <p class="abs wine-notes">Flavor profile: ectetur, adipisci velit, sed quia non numquam eius modi tempora incidunt ut labore et dolore magnam aliquam quaerat voluptatem.</p>
  <svg class="abs icon icon-pair" viewBox="0 0 24 24" fill="none" stroke="#5c1732" stroke-width="1.5"><circle cx="12" cy="12" r="11"/><path d="M6 17h12M7 17v-5h10v5M9 12v-2h6v2M12 10V7"/></svg>
  <p class="abs wine-pairing">Best Pairing: Dessert</p>
</article>

<article class="abs wine-card" style="left:36px;top:1032px;width:545px;height:248px">
  <div class="abs wine-photo" role="img" aria-label="Red wine being poured into a glass" style="background:radial-gradient(ellipse at 40% 55%,#8e1c2e,#3a1418 55%,#1c1210)"></div>
  <div class="abs price-tag">Price: $14.95</div>
  <h3 class="abs wine-name" style="font-weight:400">2016 Reserve Cabarnet</h3>
  <svg class="abs icon icon-flavor" viewBox="0 0 24 24" fill="none" stroke="#5c1732" stroke-width="1.5"><circle cx="12" cy="12" r="11"/><path d="M8 6h8c0 4-2 6-4 6s-4-2-4-6zM12 12v6M9 18h6"/></svg>
  <p class="abs wine-notes">Flavor profile: ectetur, adipisci velit, sed quia non numquam eius modi tempora incidunt ut labore et dolore magnam aliquam quaerat voluptatem.</p>
  <svg class="abs icon icon-pair" viewBox="0 0 24 24" fill="none" stroke="#5c1732" stroke-width="1.5"><circle cx="12" cy="12" r="11"/><path d="M6 16l12-6v6zM10 14.5v.5M14 13v.5"/></svg>
  <p class="abs wine-pairing">Best Pairing: Cheese</p>
</article>

<article class="abs wine-card" style="left:607px;top:1032px;width:554px;height:248px">
  <div class="abs wine-photo" role="img" aria-label="Glass of white wine against a bright background" style="background:linear-gradient(180deg,#e4e2dc,#c9c1a8 60%,#8a8068)"></div>
  <div class="abs price-tag">Price: $14.95</div>
  <h3 class="abs wine-name" style="font-weight:400">2016 Reserve Cabarnet</h3>
  <svg class="abs icon icon-flavor" viewBox="0 0 24 24" fill="none" stroke="#5c1732" stroke-width="1.5"><circle cx="12" cy="12" r="11"/><path d="M8 6h8c0 4-2 6-4 6s-4-2-4-6zM12 12v6M9 18h6"/></svg>
  <p class="abs wine-notes">Flavor profile: ectetur, adipisci velit, sed quia non numquam eius modi tempora incidunt ut labore et dolore magnam aliquam quaerat voluptatem.</p>
  <svg class="abs icon icon-pair" viewBox="0 0 24 24" fill="none" stroke="#5c1732" stroke-width="1.5"><circle cx="12" cy="12" r="11"/><path d="M6 17h12M7 17v-5h10v5M9 12v-2h6v2M12 10V7"/></svg>
  <p class="abs wine-pairing">Best Pairing: Dessert</p>
</article>

<h2 class="abs band" style="top:1322px;font-weight:400">Our Story</h2>

<section class="abs story" role="img" aria-label="Faded photo of wine glasses in soft light behind the story text">
  <div class="abs story-text">
    <p>Maranoola is a family owned company, we grow the gapes, and make the wine in the Clare valley. Daniel Whitlock is the winemaker and is well known for his style, which is all about the fruit flavour rather than wood or age influences.</p>
    <p>Maranoola is Abriginal for 2 hills and a water source. We hand pick, hand plunge, foot crush resulting in elegant wine. Little to no additives, minimal filtering, single vineyard wines. Handcrafted with small releases of only the best fruit from carefully selected rows and bunches.</p>
    <p>The Clare valley is located two hours North of Adelaide, is known for cool climate and slow ripening, resulting in wines that have an elegant mouth feel, with bright colour and outstanding flavours.</p>
    <p>Our Brookmere vineyard has a Eastern aspect, gathering morning sun and escaping the hot afternoons, and in our opinion is on of the prettiest valleys in the world. Only 1000 cases per annum of the very best handpicked fruit, from the best rows.</p>
    <p>We hope you enjoy the Maranoola style, the reds are lighter in colour, fruit driven palate, more old world influence and the Riesling is on the dry side with fresh citrus. Minimal additives and filtering, our aim was to make wine with minimal influence from wine making. Handcrafted wines.</p>
  </div>
</section>

<h2 class="abs band" style="top:1825px;font-weight:400">Galery</h2>

<div class="abs gallery-item g-vines" style="left:54px;top:1983px" role="img" aria-label="Grape vines on a wooden trellis"></div>
<div class="abs gallery-item g-pour" style="left:425px;top:1983px" role="img" aria-label="Red wine poured into a glass"></div>
<div class="abs gallery-item g-bottles" style="left:793px;top:1983px" role="img" aria-label="Row of red wine bottles on a table"></div>
<div class="abs gallery-item g-vines" style="left:54px;top:2242px" role="img" aria-label="Grape vines on a wooden trellis"></div>
<div class="abs gallery-item g-pour" style="left:425px;top:2242px" role="img" aria-label="Red wine poured into a glass"></div>
<div class="abs gallery-item g-bottles" style="left:793px;top:2242px" role="img" aria-label="Row of red wine bottles on a table"></div>
<div class="abs gallery-item g-vines" style="left:54px;top:2504px" role="img" aria-label="Grape vines on a wooden trellis"></div>
<div class="abs gallery-item g-pour" style="left:425px;top:2504px" role="img" aria-label="Red wine poured into a glass"></div>
<div class="abs gallery-item g-bottles" style="left:793px;top:2504px" role="img" aria-label="Row of red wine bottles on a table"></div>

<h2 class="abs band" style="top:2836px;font-weight:400">Contact Us</h2>

<div class="abs field" style="top:2994px;height:36px">Name</div>
<div class="abs field" style="top:3066px;height:37px">Email</div>
<div class="abs field" style="top:3139px;height:166px;padding-top:12px">Message</div>
<a class="abs btn send-btn">Send</a>

<h2 class="abs band" style="top:3497px;font-weight:400">Follow Us</h2>

<a class="abs social" style="left:430px" aria-label="Social link"></a>
<a class="abs social" style="left:560px" aria-label="Social link"></a>
<a class="abs social" style="left:689px" aria-label="Social link"></a>

<footer class="abs footer"></footer>

</body>
</html>
```